Business card for medical clinic

I need an upmarket, modern medical/health business card for my clinic

Contact Information for Business Card

name, address, email, qr code

```html
<!DOCTYPE html>
<html lang="en">
<head>
<meta charset="utf-8">
<title>Meridian Care Clinic – Business Card</title>
<link href="https://fonts.googleapis.com/css2?family=Cinzel:wght@600&family=Crimson+Text:wght@400;600&display=swap" rel="stylesheet">
<style>
  :root {
    --backdrop: #2c2c2e;
    --card: #f7f7f6;
    --navy: #1d3f6e;
    --blue: #1e8fd0;
    --blue-deep: #17527f;
    --ink: #555b63;
  }
  * { margin: 0; padding: 0; box-sizing: border-box; }
  html, body {
    width: 1200px; height: 852px; overflow: hidden;
    background: var(--backdrop);
  }
  .stage { position: relative; width: 1200px; height: 852px; }

  .card {
    position: absolute;
    width: 500px; height: 286px;
    background: var(--card);
    border-radius: 18px;
    overflow: hidden;
    box-shadow: 0 14px 30px rgba(0,0,0,.45);
  }
  .card--front { left: 70px; top: 283px; }
  .card--back { left: 630px; top: 283px; }

  .card__edge {
    position: absolute; left: 0; right: 0; bottom: 0; height: 7px;
    background: linear-gradient(90deg, var(--navy), var(--blue));
  }

  .brand { display: flex; align-items: center; gap: 12px; }
  .brand__dot {
    width: 14px; height: 14px; border-radius: 50%;
    background: var(--blue);
    flex: none;
  }
  .brand__name {
    font-family: "Cinzel", serif;
    font-weight: 600;
    color: var(--navy);
    letter-spacing: .04em;
    line-height: 1.1;
  }
  .card--front .brand {
    position: absolute; left: 0; right: 0; top: 126px; justify-content: center;
  }
  .card--front .brand__name { font-size: 27px; }

  .card--back .brand { position: absolute; left: 36px; top: 58px; }
  .card--back .brand__name { font-size: 22px; width: 200px; }

  .contact {
    position: absolute; left: 292px; top: 46px; width: 190px;
    list-style: none;
    font-family: "Crimson Text", serif;
    font-size: 13px; color: var(--ink);
  }
  .contact li { display: flex; align-items: center; gap: 8px; height: 19px; white-space: nowrap; }
  .contact svg { width: 11px; height: 11px; fill: var(--blue-deep); flex: none; }
  .contact .contact__address { margin-top: 4px; }

  .person {
    position: absolute; left: 36px; bottom: 46px;
    font-family: "Crimson Text", serif;
  }
  .person__name {
    font-family: "Cinzel", serif; font-weight: 600;
    font-size: 19px; color: var(--navy); letter-spacing: .03em;
  }
  .person__role { font-size: 14px; color: var(--ink); margin-top: -2px; }

  .tab {
    position: absolute; right: 0; bottom: 0;
    width: 250px; height: 54px;
    background: linear-gradient(90deg, var(--blue-deep), var(--blue) 60%, #147ab6);
    border-top-left-radius: 12px;
    display: flex; align-items: center; justify-content: center;
    font-family: "Crimson Text", serif; font-weight: 600;
    font-size: 14px; letter-spacing: .14em; color: #eef6fc;
    padding-bottom: 6px;
  }
</style>
</head>
<body>
<main class="stage">

  <section class="card card--front" aria-label="Card front">
    <div class="brand">
      <span class="brand__dot"></span>
      <span class="brand__name">MERIDIAN CARE CLINIC</span>
    </div>
    <div class="card__edge"></div>
  </section>

  <section class="card card--back" aria-label="Card back">
    <div class="brand">
      <span class="brand__dot"></span>
      <span class="brand__name">MERIDIAN CARE CLINIC</span>
    </div>

    <ul class="contact">
      <li>
        <svg viewBox="0 0 24 24"><path d="M6.6 10.8a15.1 15.1 0 0 0 6.6 6.6l2.2-2.2a1 1 0 0 1 1-.25 11.4 11.4 0 0 0 3.6.57 1 1 0 0 1 1 1V20a1 1 0 0 1-1 1A17 17 0 0 1 3 4a1 1 0 0 1 1-1h3.5a1 1 0 0 1 1 1c0 1.25.2 2.45.57 3.57a1 1 0 0 1-.25 1z"/></svg>
        0555-240-13690
      </li>
      <li>
        <svg viewBox="0 0 24 24"><path d="M2 5h20v14H2z M2 5l10 8 10-8" stroke="#f7f7f6" stroke-width="1.5"/></svg>
        hello@meridiancare.com
      </li>
      <li>
        <svg viewBox="0 0 24 24"><circle cx="12" cy="12" r="10"/></svg>
        www.meridiancare.com
      </li>
      <li class="contact__address">48 Elm Row, Ashford, US 20415</li>
    </ul>

    <div class="person">
      <div class="person__name">DANIEL HART</div>
      <div class="person__role">Managing Director</div>
    </div>

    <div class="card__edge"></div>
    <div class="tab">MERIDIAN CARE CLINIC</div>
  </section>

</main>
</body>
</html>
```